Quote Cards With KB May 2025 for Instagram

I would like to put these quotes over one of the pictures attached; Instagram (new size: 4:5 (1080 x 1350 pixels) One Quote per picture, and I want the quote to be bold or easy to read as well. I provided a few reference graphics that I really like as examples below. In very small letters at the bottom add @KBHarlowOnline

All of the pictures are attached; you can pick any photo and add one quote to it; but no stock photography

```html
<!DOCTYPE html>
<html lang="en">
<head>
<meta charset="utf-8">
<title>Quote Cards With KB — May 2025</title>
<link href="https://fonts.googleapis.com/css2?family=Oswald:wght@400;500&family=Poppins:wght@400;500&display=swap" rel="stylesheet">
<style>
  :root {
    --page-bg: #ffffff;
    --panel: rgba(92, 34, 68, 0.86);
    --quote-ink: #fbf3ea;
    --handle-ink: #f3e6ee;
    --rule: rgba(243, 230, 238, 0.85);
  }
  * { box-sizing: border-box; margin: 0; padding: 0; }
  html, body {
    width: 1200px;
    height: 3352px;
    overflow: hidden;
    background: var(--page-bg);
  }
  .board {
    position: relative;
    width: 1200px;
    height: 3352px;
  }
  .card {
    position: absolute;
    width: 497px;
    height: 621px;
    overflow: hidden;
  }
  .col-a { left: 99px; }
  .col-b { left: 603px; }
  .row-1 { top: 102px; }
  .row-2 { top: 730px; }
  .row-3 { top: 1363px; }
  .row-4 { top: 1995px; }
  .row-5 { top: 2628px; }

  .photo {
    position: absolute;
    inset: 0;
  }
  .photo-studio   { background: linear-gradient(160deg, #8b7f86 0%, #5d4c57 45%, #2a2228 100%); }
  .photo-court    { background: linear-gradient(170deg, #6d5f8a 0%, #a58a6a 55%, #6a4d3a 100%); }
  .photo-gala     { background: linear-gradient(150deg, #e9a9b8 0%, #c04aa0 45%, #8e5aa8 100%); }
  .photo-flowers  { background: linear-gradient(170deg, #b8c3d6 0%, #b58097 50%, #b88a3a 100%); }
  .photo-home     { background: linear-gradient(165deg, #e8e2e4 0%, #c9bfc4 55%, #2b262a 100%); }
  .photo-stands   { background: linear-gradient(165deg, #a897b0 0%, #9c6a8c 45%, #3a2d38 100%); }
  .photo-garden-a { background: linear-gradient(170deg, #ddd3e0 0%, #b7a3b8 50%, #4f4638 100%); }
  .photo-garden-b { background: linear-gradient(170deg, #e7dfe8 0%, #c3b4c4 50%, #5b5040 100%); }
  .photo-lounge-a { background: linear-gradient(165deg, #efe6ec 0%, #c9b3c3 55%, #2a2227 100%); }
  .photo-lounge-b { background: linear-gradient(165deg, #e4d7df 0%, #bfa9b8 55%, #251f23 100%); }

  .quote-panel {
    position: absolute;
    left: 196px;
    top: 44px;
    width: 275px;
    height: 533px;
    background: var(--panel);
    border-radius: 16px;
    display: flex;
    flex-direction: column;
  }
  .quote {
    flex: 1;
    display: flex;
    align-items: center;
    justify-content: center;
    text-align: center;
    font-family: "Oswald", sans-serif;
    font-weight: 400;
    font-size: 35px;
    line-height: 47px;
    letter-spacing: -0.4px;
    text-transform: uppercase;
    color: var(--quote-ink);
    white-space: nowrap;
    padding-top: 10px;
  }
  .handle {
    display: flex;
    align-items: center;
    gap: 10px;
    height: 22px;
    margin: 0 -22px 42px -22px;
    font-family: "Poppins", sans-serif;
    font-size: 15px;
    font-weight: 500;
    color: var(--handle-ink);
    white-space: nowrap;
  }
  .handle::before,
  .handle::after {
    content: "";
    flex: 1;
    height: 1.5px;
    background: var(--rule);
  }
</style>
</head>
<body>
<main class="board">

  <article class="card col-a row-1">
    <div class="photo photo-studio" role="img" aria-label="KB posing in a sheer black top and black jeans in a studio"></div>
    <div class="quote-panel">
      <p class="quote">Tired. Moody.<br>Stubborn belly<br>fat. Your<br>hormones are<br>screaming<br>for help!<br>Let’s fix that.</p>
      <p class="handle">@KBHarlowOnline</p>
    </div>
  </article>

  <article class="card col-b row-1">
    <div class="photo photo-court" role="img" aria-label="KB standing courtside in a sparkly top and black jeans"></div>
    <div class="quote-panel">
      <p class="quote">That stubborn<br>weight? It’s not<br>your fault.<br>Your hormones<br>are to blame<br>and you’re<br>not alone;<br>but there<br>is a fix.</p>
      <p class="handle">@KBHarlowOnline</p>
    </div>
  </article>

  <article class="card col-a row-2">
    <div class="photo photo-gala" role="img" aria-label="KB in a long magenta gown at a gala"></div>
    <div class="quote-panel">
      <p class="quote">Your belly<br>isn’t fat…<br>it’s hormonal.<br>And here’s<br>how to fix it.<br>Comment<br>hormones<br>if nothing<br>is working.</p>
      <p class="handle">@KBHarlowOnline</p>
    </div>
  </article>

  <article class="card col-b row-2">
    <div class="photo photo-flowers" role="img" aria-label="KB in a pink fitted dress in front of a sunflower display"></div>
    <div class="quote-panel">
      <p class="quote">The stubborn<br>belly fat<br>after 40?<br>It’s not<br>about calories;<br>it’s about<br>your hormones.<br>Here is the fix!</p>
      <p class="handle">@KBHarlowOnline</p>
    </div>
  </article>

  <article class="card col-a row-3">
    <div class="photo photo-home" role="img" aria-label="KB in a white crop sweater and black pants at home"></div>
    <div class="quote-panel">
      <p class="quote">Flat tummy<br>in your 40s?<br>It’s still<br>possible!<br>Comment<br>bye belly<br>to get the<br>10 secrets to a<br>flatter tummy</p>
      <p class="handle">@KBHarlowOnline</p>
    </div>
  </article>

  <article class="card col-b row-3">
    <div class="photo photo-stands" role="img" aria-label="KB seated courtside holding a basketball"></div>
    <div class="quote-panel">
      <p class="quote">Bloating.<br>Muffin top.<br>Puffy waistline.<br>Your body’s<br>screaming<br>for a different<br>kind of fix.<br>Here it is</p>
      <p class="handle">@KBHarlowOnline</p>
    </div>
  </article>

  <article class="card col-a row-4">
    <div class="photo photo-garden-a" role="img" aria-label="KB smiling in a black top outdoors"></div>
    <div class="quote-panel">
      <p class="quote">You’re doing<br>all the “right”<br>things, but your<br>belly won’t<br>go down?<br>Here’s what you<br>haven’t tried.</p>
      <p class="handle">@KBHarlowOnline</p>
    </div>
  </article>

  <article class="card col-b row-4">
    <div class="photo photo-garden-b" role="img" aria-label="KB in a sheer black top and jeans, side pose outdoors"></div>
    <div class="quote-panel">
      <p class="quote">This 90-day plan<br>helped women<br>over 40 slim<br>down, get a<br>tiny waist and<br>feel sexy again.<br>You’re next.</p>
      <p class="handle">@KBHarlowOnline</p>
    </div>
  </article>

  <article class="card col-a row-5">
    <div class="photo photo-lounge-a" role="img" aria-label="KB in a sheer striped black top posing indoors"></div>
    <div class="quote-panel">
      <p class="quote">This is the<br>secret women<br>over 40 are<br>using to<br>get snatched;<br>without starving.<br>Comment skinny<br>to get the<br>exact plan.</p>
      <p class="handle">@KBHarlowOnline</p>
    </div>
  </article>

  <article class="card col-b row-5">
    <div class="photo photo-lounge-b" role="img" aria-label="KB in a sheer striped black top with high-waist jeans indoors"></div>
    <div class="quote-panel">
      <p class="quote">What worked in<br>your 30s won’t<br>work now.<br>Here’s what<br>actually does.<br>Drop 30 pounds<br>in 3 months.</p>
      <p class="handle">@KBHarlowOnline</p>
    </div>
  </article>

</main>
</body>
</html>
```